Harbourview Bat Club

I am looking to develop a sponsorship proposal using some of the imagery and colours 'black and gold' into a classy, professional laid out document to present to potential sponsors.
The content for the proposal/presentation is detailed in the "HBC Sponsor Deck". The HBC logo is featured in the black & gold presentations.

```html
<!DOCTYPE html>
<html lang="en">
<head>
<meta charset="utf-8">
<title>HBC Sponsor Deck</title>
<link href="https://fonts.googleapis.com/css2?family=Cinzel:wght@400;500&family=Poppins:wght@400;500;600&display=swap" rel="stylesheet">
<style>
:root{
  --ink:#151312;
  --gold:#7d5f3b;
  --gold-light:#a88458;
  --paper:#ffffff;
  --panel:#f3f2f1;
  --text:#2a2623;
  --board:#e4e4e4;
}
*{box-sizing:border-box;margin:0;padding:0}
html,body{width:1013px;height:1200px;overflow:hidden;background:var(--board)}
body{position:relative;font-family:'Poppins',sans-serif;color:var(--text)}
.slot{position:absolute;width:410px;height:231px;box-shadow:0 3px 8px rgba(0,0,0,.18)}
.slide{position:absolute;left:0;top:0;width:715px;height:402px;transform:scale(.5734);transform-origin:0 0;background:var(--paper);overflow:hidden}
.frame{position:absolute;inset:0;width:715px;height:402px}
.corner-mark{position:absolute;right:14px;top:14px;font:600 11px 'Poppins',sans-serif;color:var(--gold);letter-spacing:.5px}
.pg{position:absolute;right:22px;bottom:14px;font-size:8px;color:var(--text)}
.title{position:absolute;left:22px;font-family:'Cinzel',serif;font-weight:400;font-size:24px;line-height:25px;color:var(--ink)}
.title::after{content:"";display:block;width:66px;height:1.5px;background:var(--ink);margin-top:9px}
.lead{position:absolute;font-size:9.5px;font-weight:600;color:var(--ink)}
.body{position:absolute;font-size:9.5px;line-height:15px}
ul.dots{list-style:none;font-size:9.5px;line-height:19px}
ul.dots li{position:relative;padding-left:13px}
ul.dots li::before{content:"";position:absolute;left:0;top:7px;width:5px;height:5px;border-radius:50%;background:var(--gold)}
.panel{position:absolute;background:var(--panel);border-radius:12px}
.photo{position:absolute;border-radius:12px}
.cover{background:var(--ink)}
.cover .photo{border-radius:0}
.brand{position:absolute;text-align:center;font-family:'Poppins',sans-serif;font-weight:500;color:var(--gold-light)}
.brand .ring{display:block;margin:0 auto 10px;width:54px;height:54px;border-radius:50%;border:2px solid var(--gold-light)}
.brand .name{font-size:13px;letter-spacing:1.5px;line-height:16px}
.cover-title{position:absolute;text-align:center;font-family:'Cinzel',serif;color:#fff;font-size:27px;line-height:37px}
.feature{position:absolute;left:22px;display:flex;align-items:center;gap:14px;font-size:13px;color:var(--ink)}
.feature .disc{width:52px;height:52px;border-radius:50%;background:var(--gold);display:flex;align-items:center;justify-content:center}
.choice{position:absolute;border-radius:14px;color:#fff}
.choice h3,.panel h3{font-size:13px;font-weight:600}
.choice ul.dots li::before{background:var(--gold-light)}
.choice.gold ul.dots li::before{background:var(--ink)}
.card{position:absolute;top:142px;width:214px;height:218px;background:var(--panel);border-radius:12px;padding:24px 17px}
.card h4{font-size:13px;font-weight:600;line-height:15px;color:var(--ink);margin:16px 0 16px}
.card p{font-size:9.5px;line-height:15px}
.closing{position:absolute;left:390px;width:300px;text-align:center;color:#fff;font-size:9.5px;line-height:15px}
.closing h2{font-family:'Cinzel',serif;font-weight:400;font-size:24px;line-height:30px;margin-bottom:12px}
.closing p{margin-bottom:6px}
.closing b{font-weight:600}
</style>
</head>
<body>

<!-- Cover -->
<div class="slot" style="left:78px;top:89px">
  <div class="slide cover">
    <div class="photo" role="img" aria-label="Batsman in helmet and whites gripping a bat on a green field" style="left:0;top:0;width:500px;height:402px;background:linear-gradient(110deg,#f1ede6 0%,#c9c1b3 30%,#6d7a48 60%,#3f4f2a 100%)"></div>
    <svg class="frame" viewBox="0 0 715 402"><path d="M470 0H715V402H400Q330 190 470 0Z" fill="var(--ink)"/></svg>
    <div class="brand" style="left:474px;top:62px;width:200px"><span class="ring"></span><div class="name">HARBOURVIEW<br>BAT CLUB</div></div>
    <div class="cover-title" style="left:440px;top:196px;width:270px">Corporate<br>Partnership &amp;<br>Hospitality<br>Opportunities</div>
  </div>
</div>

<!-- Signature experience -->
<div class="slot" style="left:524px;top:89px">
  <div class="slide">
    <svg class="frame" viewBox="0 0 715 402">
      <path d="M0 0H715V55Q420 -5 0 30Z" fill="var(--ink)"/>
      <path d="M0 30Q420 -5 715 55V80Q420 12 0 30Z" fill="var(--gold)"/>
      <path d="M0 360Q90 392 200 402H0Z" fill="var(--gold)"/>
    </svg>
    <span class="corner-mark">HBC</span>
    <h1 class="title" style="top:142px">Signature<br>Experience</h1>
    <p class="lead" style="left:22px;top:226px">Silver Service Lunch in the Players' Dressing Room</p>
    <p class="body" style="left:22px;top:252px;width:260px">Host twelve of your most valued clients inside one of Australia's most famous sporting venues.</p>
    <div class="panel" style="left:357px;top:92px;width:285px;height:263px;padding:32px 17px">
      <h3 style="color:var(--ink)">Includes</h3>
      <ul class="dots" style="margin-top:12px">
        <li>Private silver-service luncheon</li>
        <li>Exclusive access to players' dressing room</li>
        <li>Cricket guest speaker</li>
        <li>Behind-the-scenes stories</li>
        <li>Premium wines</li>
        <li>Professional photographs</li>
      </ul>
      <p class="body" style="position:static;margin-top:16px">This is not available through traditional<br>corporate hospitality.</p>
    </div>
    <span class="pg">Pg: 05</span>
  </div>
</div>

<!-- More than cricket -->
<div class="slot" style="left:78px;top:352px">
  <div class="slide">
    <svg class="frame" viewBox="0 0 715 402">
      <path d="M0 0H715V55Q420 -5 0 22Z" fill="var(--ink)"/>
      <path d="M0 22Q420 -5 715 55V80Q420 12 0 22Z" fill="var(--gold)"/>
      <path d="M0 360Q90 392 200 402H0Z" fill="var(--gold)"/>
    </svg>
    <span class="corner-mark">HBC</span>
    <h1 class="title" style="top:38px">More Than Cricket</h1>
    <p class="body" style="left:22px;top:106px;font-size:13px;color:var(--ink)">Invest in the game. Reward your people.</p>
    <div class="feature" style="top:144px"><span class="disc"><svg width="26" height="22" viewBox="0 0 26 22"><path d="M6 1H20L25 8L13 21L1 8Z" fill="none" stroke="#fff" stroke-width="2"/><path d="M1 8H25M9 8L13 21L17 8M6 1L9 8L13 1L17 8L20 1" fill="none" stroke="#fff" stroke-width="1.5"/></svg></span>Premium Hospitality</div>
    <div class="feature" style="top:207px"><span class="disc"><svg width="24" height="18" viewBox="0 0 24 18"><path d="M1 3L7 9L12 1L17 9L23 3L21 13H3Z" fill="#fff"/><rect x="3" y="15" width="18" height="3" fill="#fff"/></svg></span>Exclusive Experiences</div>
    <div class="feature" style="top:270px"><span class="disc"><svg width="28" height="20" viewBox="0 0 28 20"><circle cx="14" cy="5" r="4" fill="#fff"/><circle cx="5" cy="7" r="3" fill="#fff"/><circle cx="23" cy="7" r="3" fill="#fff"/><path d="M7 19Q7 10 14 10Q21 10 21 19Z" fill="#fff"/><path d="M0 18Q0 11 5 11Q8 11 8 13L6 18ZM28 18Q28 11 23 11Q20 11 20 13L22 18Z" fill="#fff"/></svg></span>Community Impact</div>
    <div class="photo" role="img" aria-label="Striped cricket oval with trees and light tower under a blue sky" style="left:382px;top:82px;width:310px;height:262px;background:linear-gradient(180deg,#3d73c4 0%,#a9c6e8 35%,#3e6a33 55%,#6d9a3e 80%,#4b6b2e 100%)"></div>
    <span class="pg">Pg: 02</span>
  </div>
</div>

<!-- Corporate suite -->
<div class="slot" style="left:524px;top:352px">
  <div class="slide">
    <svg class="frame" viewBox="0 0 715 402">
      <path d="M0 0H715V55Q420 -5 0 22Z" fill="var(--ink)"/>
      <path d="M0 22Q420 -5 715 55V80Q420 12 0 22Z" fill="var(--gold)"/>
      <path d="M0 360Q90 392 200 402H0Z" fill="var(--gold)"/>
    </svg>
    <span class="corner-mark">HBC</span>
    <h1 class="title" style="top:38px">Corporate Suite Experiences</h1>
    <p class="lead" style="left:22px;top:84px">Reward staff or entertain clients throughout the year.</p>
    <div class="choice" style="left:22px;top:120px;width:310px;height:175px;background:var(--ink);padding:24px 28px">
      <h3>Choose from</h3>
      <ul class="dots" style="margin-top:12px">
        <li>International Test Cricket</li>
        <li>Harbour Hawks T20</li>
        <li>Harbour Kites Football</li>
        <li>Major rugby league fixture</li>
      </ul>
    </div>
    <div class="choice gold" style="left:380px;top:120px;width:312px;height:175px;background:var(--gold);padding:24px 0 0 126px">
      <h3>Includes</h3>
      <ul class="dots" style="margin-top:12px">
        <li>Premium corporate suite</li>
        <li>Catering</li>
        <li>Premium beverages</li>
        <li>Reserved seating</li>
        <li>Dedicated host</li>
      </ul>
    </div>
    <div class="photo" role="img" aria-label="Team photo of cricketers in whites in front of a pavilion" style="left:250px;top:109px;width:200px;height:200px;border-radius:50%;background:radial-gradient(circle at 50% 45%,#e8e4dc 0%,#9a9a8a 40%,#3f5a2c 75%,#2f4020 100%)"></div>
    <p class="body" style="left:22px;top:333px;width:560px">Multiple events can be bundled into annual partnership packages. The HCG offers a range of premium hospitality formats including private suites and other premium entertaining options for cricket and football events.</p>
    <span class="pg">Pg: 06</span>
  </div>
</div>

<!-- Why club -->
<div class="slot" style="left:78px;top:616px">
  <div class="slide">
    <svg class="frame" viewBox="0 0 715 402">
      <path d="M0 0H715V55Q420 -5 0 22Z" fill="var(--ink)"/>
      <path d="M0 22Q420 -5 715 55V80Q420 12 0 22Z" fill="var(--gold)"/>
      <path d="M0 360Q90 392 200 402H0Z" fill="var(--gold)"/>
    </svg>
    <span class="corner-mark">HBC</span>
    <h1 class="title" style="top:38px">Why Harbourview Bat Club?</h1>
    <p class="body" style="left:22px;top:98px;width:320px">Harbourview Bat Club is one of Australia's oldest &amp; most respected cricket clubs.</p>
    <p class="body" style="left:22px;top:131px;width:320px">Founded in 1897, we are a not-for-profit organisation dedicated to growing cricket across Sydney and New South Wales.</p>
    <div class="photo" role="img" aria-label="Wicketkeeper and bowler in action beside the stumps and a lattice fence" style="left:22px;top:183px;width:312px;height:174px;background:linear-gradient(90deg,#3a6fb0 0%,#cfd6df 40%,#efece6 60%,#c8b894 100%)"></div>
    <p class="body" style="left:375px;top:98px;width:300px">Every dollar generated through sponsorship is reinvested directly into:</p>
    <ul class="dots" style="position:absolute;left:375px;top:133px">
      <li>Men's and Women's Premier Cricket</li>
      <li>Junior Development Programs</li>
      <li>Community Coaching</li>
      <li>Youth Academies</li>
      <li>Female Participation</li>
      <li>Multicultural Cricket</li>
      <li>Facilities at Riverside Oval</li>
    </ul>
    <p class="body" style="left:375px;top:276px;width:300px">Unlike many sponsorships, your investment doesn't simply buy hospitality.</p>
    <p class="body" style="left:375px;top:310px;width:300px">It helps create opportunities for hundreds of young cricketers while connecting your business with one of Australia's most iconic sporting institutions.</p>
    <span class="pg">Pg: 03</span>
  </div>
</div>

<!-- Play where greats play -->
<div class="slot" style="left:524px;top:616px">
  <div class="slide">
    <svg class="frame" viewBox="0 0 715 402">
      <path d="M0 0H715V55Q420 -5 0 22Z" fill="var(--ink)"/>
      <path d="M0 22Q420 -5 715 55V80Q420 12 0 22Z" fill="var(--gold)"/>
      <path d="M0 360Q90 392 200 402H0Z" fill="var(--gold)"/>
    </svg>
    <span class="corner-mark">HBC</span>
    <h1 class="title" style="top:38px">Play Where Australia's<br>Greats Play</h1>
    <p class="lead" style="left:22px;top:113px">A once-in-a-lifetime experience.</p>
    <p class="body" style="left:22px;top:128px">Twenty corporate guests plus one child per guest enjoy:</p>
    <div class="panel" style="left:22px;top:160px;width:285px;height:155px;padding:18px 17px">
      <ul class="dots">
        <li>Exclusive HCG net session</li>
        <li>Australian cricketer host</li>
        <li>Coaching clinic</li>
        <li>Family participation</li>
        <li>BBQ overlooking the ground</li>
        <li>Professional photos</li>
      </ul>
    </div>
    <p class="body" style="left:22px;top:328px">A memory your clients and their families will never forget.</p>
    <div class="photo" role="img" aria-label="Young batsman playing a shot at the crease with a bowler and fielder behind" style="left:357px;top:100px;width:335px;height:250px;background:linear-gradient(180deg,#1f2e1a 0%,#34502a 45%,#7ea34a 75%,#6b8f3c 100%)"></div>
    <span class="pg">Pg: 05</span>
  </div>
</div>

<!-- Why partner -->
<div class="slot" style="left:78px;top:879px">
  <div class="slide">
    <svg class="frame" viewBox="0 0 715 402">
      <path d="M0 0H715V55Q420 -5 0 22Z" fill="var(--ink)"/>
      <path d="M0 22Q420 -5 715 55V80Q420 12 0 22Z" fill="var(--gold)"/>
      <path d="M0 360Q90 392 200 402H0Z" fill="var(--gold)"/>
    </svg>
    <span class="corner-mark">HBC</span>
    <h1 class="title" style="top:38px">Why Partner With Harbourview<br>Bat Club?</h1>
    <p class="body" style="left:22px;top:109px">Three reasons make Harbourview Bat Club unique.</p>
    <div class="card" style="left:22px">
      <svg width="32" height="36" viewBox="0 0 32 36"><circle cx="16" cy="14" r="12" fill="none" stroke="var(--gold)" stroke-width="3"/><rect x="11" y="12" width="10" height="8" rx="1" fill="var(--gold)"/><path d="M13 12V9a3 3 0 016 0v3" fill="none" stroke="var(--gold)" stroke-width="2"/><path d="M8 24L5 35L11 31L13 26M24 24L27 35L21 31L19 26" fill="var(--gold)"/></svg>
      <h4>Exclusive<br>Access</h4>
      <p>Our relationship with the Harbour Cricket Ground and Eastgate Stadium enables us to create experiences that very few sporting organisations can provide.</p>
    </div>
    <div class="card" style="left:250px">
      <svg width="32" height="36" viewBox="0 0 32 36"><circle cx="21" cy="5" r="4" fill="var(--gold)"/><path d="M17 11H25L26 24L23 35H20L20 24L17 20Z" fill="var(--gold)"/><path d="M18 15L3 32" stroke="var(--gold)" stroke-width="4" stroke-linecap="round"/></svg>
      <h4>Australia's Leading<br>Women's Cricket Club</h4>
      <p>Few clubs have produced more Australian and NSW women's cricketers, including Mia Calloway, Tessa Marlowe, Jodie Penfold and Rosa Whitcombe.</p>
    </div>
    <div class="card" style="left:478px">
      <svg width="40" height="30" viewBox="0 0 40 30"><circle cx="20" cy="7" r="6" fill="var(--gold)"/><circle cx="7" cy="10" r="4.5" fill="var(--gold)"/><circle cx="33" cy="10" r="4.5" fill="var(--gold)"/><path d="M10 29Q10 15 20 15Q30 15 30 29Z" fill="var(--gold)"/><path d="M0 27Q0 17 7 17Q11 17 11 20L9 27ZM40 27Q40 17 33 17Q29 17 29 20L31 27Z" fill="var(--gold)"/></svg>
      <h4>Genuine Community<br>Impact</h4>
      <p>Every partnership supports local cricket, junior development and the next generation of players across Sydney.</p>
    </div>
    <span class="pg">Pg: 04</span>
  </div>
</div>

<!-- Closing -->
<div class="slot" style="left:524px;top:879px">
  <div class="slide cover">
    <div class="photo" role="img" aria-label="Batsman in helmet and whites ready to play a shot on a green field" style="left:0;top:0;width:500px;height:402px;background:linear-gradient(110deg,#f1ede6 0%,#c9c1b3 30%,#6d7a48 60%,#3f4f2a 100%)"></div>
    <svg class="frame" viewBox="0 0 715 402"><path d="M470 0H715V402H400Q330 190 470 0Z" fill="var(--ink)"/></svg>
    <div class="brand" style="left:440px;top:26px;width:200px"><span class="ring"></span><div class="name">HARBOURVIEW<br>BAT CLUB</div></div>
    <div class="closing" style="top:152px">
      <h2>Let's Build<br>Something Together</h2>
      <p>When your business partners with Harbourview Bat Club, you become part of something much larger than cricket.</p>
      <p><b>You help build stronger communities.</b></p>
      <p>Develop future Australian representatives.<br>Create unforgettable experiences for your staff and clients.</p>
      <p><b>Together, we can grow the game.</b></p>
    </div>
  </div>
</div>

</body>
</html>
```